Print materials for 3-star hotel

We are changing up our print materials (notepads, letterheads, key card jackets, small flyer for the room rates) We are a 3 star business hotel in the Philippines and have mainly used grey tones and clean, simple lines. See attached photos for logo and hotel interior photos.

Target Market(s)

Business

Contact Information for Business Card

Corvale Terrace Hotel
Lindwell Banca Avenue corner Tolenta St Cebu City 6000 Philippines
Tel: +63 32 481 7302
Mobile: +63 917 648 2095
www.corvaleterracehotel.example

Font styles to use
Serif
Sans Serif

Requirements
Must have
• Simple
• Readable font and font size
Nice to have
• Neutral colors, grey and taupes
Should not have
• No purples and bright blues

```html
<!DOCTYPE html>
<html lang="en">
<head>
<meta charset="utf-8">
<title>Corvale Terrace Hotel – Letterhead</title>
<link rel="stylesheet" href="https://fonts.googleapis.com/css2?family=Cormorant+Garamond:wght@500&family=Montserrat:wght@600&display=swap">
<style>
  :root {
    --paper: #ffffff;
    --ink: #1c1c1c;
    --rule: #8a8a8a;
  }
  html, body {
    margin: 0;
    padding: 0;
    overflow: hidden;
    background: var(--paper);
  }
  .letterhead {
    position: relative;
    width: 849px;
    height: 1200px;
    background: var(--paper);
    overflow: hidden;
  }
  .brand-square {
    position: absolute;
    background: var(--ink);
  }
  .brand-square--top {
    left: 404px;
    top: 54px;
    width: 40px;
    height: 40px;
  }
  .brand-square--footer {
    left: 412px;
    top: 1081px;
    width: 24px;
    height: 24px;
  }
  .brand-name {
    position: absolute;
    left: 0;
    right: 0;
    top: 113px;
    margin: 0;
    text-align: center;
    font-family: "Cormorant Garamond", serif;
    font-weight: 500;
    font-size: 23px;
    letter-spacing: 0.32em;
    color: var(--ink);
    padding-left: 0.32em;
  }
  .brand-sub {
    position: absolute;
    left: 0;
    right: 0;
    top: 140px;
    text-align: center;
    font-family: "Cormorant Garamond", serif;
    font-weight: 500;
    font-size: 14px;
    letter-spacing: 0.55em;
    padding-left: 0.55em;
    color: var(--ink);
  }
  .rule {
    position: absolute;
    height: 1px;
    background: var(--rule);
  }
  .rule--head-left  { left: 62px;  top: 150px; width: 296px; }
  .rule--head-right { left: 490px; top: 150px; width: 293px; }
  .rule--foot-left  { left: 66px;  top: 1093px; width: 322px; }
  .rule--foot-right { left: 462px; top: 1093px; width: 319px; }
  .website {
    position: absolute;
    left: 0;
    right: 0;
    top: 1133px;
    text-align: center;
    font-family: "Montserrat", sans-serif;
    font-weight: 600;
    font-size: 12.5px;
    letter-spacing: 0.02em;
    color: var(--ink);
    text-transform: uppercase;
  }
</style>
</head>
<body>
  <main class="letterhead">
    <header>
      <div class="brand-square brand-square--top" aria-hidden="true"></div>
      <h1 class="brand-name">CORVALE TERRACE</h1>
      <div class="rule rule--head-left"></div>
      <div class="brand-sub">HOTEL</div>
      <div class="rule rule--head-right"></div>
    </header>
    <footer>
      <div class="rule rule--foot-left"></div>
      <div class="brand-square brand-square--footer" aria-hidden="true"></div>
      <div class="rule rule--foot-right"></div>
      <div class="website">www.corvaleterracehotel.example</div>
    </footer>
  </main>
</body>
</html>
```